Web Developer Needs a Business Card Design

I need a personal business card design that represents me as a web developer for potential employers. I would like the background to be a dark color on the front for contrast with my logo and name. The back will have all my information along with a smaller version of the logo. I want something with a modern look and feel, not too conservative. This will be used for potential employers and freelance work.

Industry/Entity Type

Business

Contact Information for Business Card

Front should have my logo and name. The back should have all my personal information which would include: name: Tom Varulek, phone: 570-614-3098, email: tomvarulek@quillbox.net, website url: www.tomvarulek.net, logo, web developer.

Font styles to use
Sans Serif

Requirements
Must have
• Must include my logo. The color palette base color will be the logo color.

```html
<!DOCTYPE html>
<html lang="en">
<head>
<meta charset="utf-8">
<title>Tom Varulek – Business Card</title>
<link href="https://fonts.googleapis.com/css2?family=Open+Sans:wght@400;600;700&display=swap" rel="stylesheet">
<style>
  :root {
    --teal: #6fcdb6;
    --teal-deep: #4fb79d;
    --charcoal: #2b2b2b;
    --charcoal-light: #4a4a4a;
    --ink: #1c1c1c;
    --paper: #ffffff;
    --stage: #ebe8e4;
    --text-light: #f2f2f2;
  }
  * { box-sizing: border-box; margin: 0; padding: 0; }
  html, body { width: 1200px; height: 913px; overflow: hidden; }
  body {
    background: var(--stage);
    font-family: "Open Sans", Arial, sans-serif;
    position: relative;
  }
  .card {
    position: absolute;
    width: 560px;
    height: 320px;
    border-radius: 22px;
    overflow: hidden;
    box-shadow: 0 6px 18px rgba(0,0,0,0.18);
  }
  .card-back { left: 40px; top: 110px; background: var(--paper); }
  .card-front {
    left: 600px; top: 480px;
    background: linear-gradient(135deg, var(--charcoal-light) 0%, var(--charcoal) 55%, var(--ink) 100%);
  }
  .card-shapes { position: absolute; inset: 0; }

  .brand-mark {
    position: absolute;
    display: flex; align-items: center; justify-content: center;
    border-radius: 50%;
    border-style: solid;
    border-color: var(--teal);
    color: var(--teal);
    font-weight: 700;
    text-align: center;
  }
  .card-back .brand-mark {
    left: 60px; top: 70px; width: 180px; height: 180px;
    border-width: 12px; font-size: 22px; line-height: 1.15;
  }
  .card-front .brand-mark {
    left: 232px; top: 40px; width: 96px; height: 96px;
    border-width: 6px; font-size: 12px; line-height: 1.15;
  }

  .contact-block {
    position: absolute; right: 28px; top: 86px;
    text-align: right; color: var(--text-light);
  }
  .contact-name { font-size: 20px; font-weight: 700; letter-spacing: 0.5px; }
  .contact-role { font-size: 12px; font-weight: 600; color: var(--teal); letter-spacing: 0.8px; margin-bottom: 14px; }
  .contact-line {
    display: flex; justify-content: flex-end; align-items: center; gap: 7px;
    font-size: 13px; line-height: 19px;
  }
  .contact-line svg { width: 11px; height: 11px; fill: var(--teal); flex: none; }
  .contact-line .icon-spacer { width: 11px; }

  .front-name {
    position: absolute; left: 0; right: 0; top: 158px;
    text-align: center; color: var(--text-light);
    font-size: 36px; font-weight: 400; letter-spacing: 3px;
  }
  .front-role {
    position: absolute; left: 0; right: 0; top: 212px;
    text-align: center; color: #d8d8d8;
    font-size: 17px; letter-spacing: 0.8px;
  }
</style>
</head>
<body>

  <section class="card card-back" aria-label="Contact side">
    <svg class="card-shapes" viewBox="0 0 560 320" preserveAspectRatio="none">
      <defs>
        <linearGradient id="panelShade" x1="0" y1="0" x2="1" y2="1">
          <stop offset="0" stop-color="#4a4a4a"/>
          <stop offset="1" stop-color="#1e1e1e"/>
        </linearGradient>
      </defs>
      <path d="M330 0 C270 70 290 210 150 320 L560 320 L560 0 Z" fill="var(--teal)"/>
      <path d="M352 0 C292 70 310 215 172 320 L560 320 L560 0 Z" fill="var(--ink)"/>
      <path d="M364 0 C304 72 322 218 186 320 L560 320 L560 0 Z" fill="url(#panelShade)"/>
    </svg>

    <div class="brand-mark">Tom<br>Varulek</div>

    <div class="contact-block">
      <div class="contact-name">TOM VARULEK</div>
      <div class="contact-role">WEB DEVELOPER</div>
      <div class="contact-line">570-614-3098
        <svg viewBox="0 0 24 24"><path d="M6.6 10.8a15.1 15.1 0 0 0 6.6 6.6l2.2-2.2a1 1 0 0 1 1-.25 11.4 11.4 0 0 0 3.6.57 1 1 0 0 1 1 1V20a1 1 0 0 1-1 1A17 17 0 0 1 3 4a1 1 0 0 1 1-1h3.5a1 1 0 0 1 1 1c0 1.25.2 2.45.57 3.57a1 1 0 0 1-.25 1z"/></svg>
      </div>
      <div class="contact-line">tomvarulek@quillbox.net
        <svg viewBox="0 0 24 24"><path d="M2 5h20v14H2z M4 7v.5l8 5 8-5V7l-8 5z" fill-rule="evenodd"/></svg>
      </div>
      <div class="contact-line">www.tomvarulek.net
        <svg viewBox="0 0 24 24"><circle cx="12" cy="12" r="10"/></svg>
      </div>
    </div>
  </section>

  <section class="card card-front" aria-label="Name side">
    <div class="brand-mark">Tom<br>Varulek</div>
    <div class="front-name">TOM VARULEK</div>
    <div class="front-role">Front-End Developer</div>
  </section>

</body>
</html>
```